Moden - Mexicali - Flower Shop

brisapetals is looking for a cool web design that has a airy, clean, mexicali feel to it.

See attached images and links for idea of what we mean with the above.

please no templates.

Target Market(s)

Local flower shop in San Diego, California

Industry/Entity Type

Shop

Requirements
Must have
• see. brisapetals.shopnest.example - I did the site and logo...I love the logo - hate the site.

Going for this feel: http://www.platetalk.example/menucraft/archives/verdanos.php

I also attached another site I liked- I just feel like it may be to busy.

```html
<!DOCTYPE html>
<html lang="en">
<head>
<meta charset="utf-8">
<title>Brisa Petals — About Us</title>
<link href="https://fonts.googleapis.com/css2?family=Fondamento&family=Merriweather:wght@400;700&family=Tinos&family=Delius&family=Rosarivo&display=swap" rel="stylesheet">
<style>
  :root {
    --page-purple: #3a1f57;
    --gold: #d9b13a;
    --panel: #bcb0c8;
    --panel-text: #7b2a8c;
    --label-green: #4f7d3a;
    --footer-bg: #2a1336;
    --footer-text: #f1ecf4;
    --tile-edge: #ffffff;
    --tile-blue: #5b93c8;
    --tile-yellow: #f3e67e;
    --tile-pink: #dd9adf;
    --tile-orange: #eea42c;
    --tile-green: #6a9c4c;
    --logo-text: #8a8aa0;
    --blog-teal: #3a8c93;
  }
  * { margin: 0; padding: 0; box-sizing: border-box; }
  html, body { width: 1095px; height: 1200px; overflow: hidden; }
  body {
    position: relative;
    background: var(--page-purple);
    font-family: "Merriweather", Georgia, serif;
  }
  .abs { position: absolute; }

  .corner-flourish {
    left: 0; top: 0; width: 160px; height: 150px;
    border-bottom-right-radius: 160px;
    background: radial-gradient(circle at 0 0, rgba(217,177,58,0.18), rgba(217,177,58,0.04) 70%, transparent 72%);
  }
  .main-nav a {
    position: absolute; font-family: "Fondamento", cursive;
    color: var(--gold); text-decoration: none; white-space: nowrap;
  }
  .nav-home { left: 176px; top: 10px; font-size: 24px; }
  .nav-shop { left: 153px; top: 62px; font-size: 24px; }
  .nav-curated { left: 102px; top: 113px; font-size: 24px; }
  .nav-about { left: 9px; top: 158px; font-size: 37px; }

  .search-box {
    left: 773px; top: 17px; width: 171px; height: 22px;
    background: rgba(255,255,255,0.35); border-radius: 2px;
    font-family: "Rosarivo", serif; font-size: 14px; color: #f2eef6;
    padding: 2px 6px; line-height: 18px;
  }
  .search-box svg { position: absolute; right: 7px; top: 4px; }
  .cart-summary {
    left: 959px; top: 13px; font-family: "Merriweather", Georgia, serif; font-size: 16px; color: #fff;
    white-space: nowrap; letter-spacing: 0.2px;
  }
  .cart-summary span { text-decoration: underline; margin-right: 11px; }
  .cart-summary span:last-child { margin-right: 0; }
  .view-cart { left: 988px; top: 46px; font-family: "Rosarivo", serif; font-size: 17px; color: #fff; }

  .crest-ornament {
    left: 488px; top: 34px; width: 119px; height: 46px;
    border-radius: 60px 60px 6px 6px;
    background: linear-gradient(180deg, rgba(217,177,58,0.35), rgba(217,177,58,0.12));
  }
  .logo-frame {
    left: 380px; top: 80px; width: 334px; height: 93px;
    border: 1px solid var(--gold);
  }
  .logo-plate {
    position: absolute; left: 5px; top: 4px; right: 4px; bottom: 4px;
    background: #fff; display: flex; align-items: center; justify-content: center;
    font-family: "Rosarivo", serif; font-size: 26px; letter-spacing: 6px; color: var(--logo-text);
  }

  .content-frame {
    left: 147px; top: 203px; width: 803px; height: 707px;
    border: 2px solid var(--gold);
  }
  .content-panel {
    position: absolute; left: 4px; top: 4px; right: 4px; bottom: 4px;
    background: var(--panel);
  }
  .page-title {
    left: 169px; top: 226px; font-family: "Tinos", serif; font-weight: 400;
    font-size: 35px; color: #111;
  }
  .intro {
    left: 171px; top: 281px; font-family: "Rosarivo", serif; font-size: 16px;
    line-height: 22px; color: var(--panel-text);
  }

  .feature { position: absolute; width: 200px; text-align: center; }
  .tile {
    width: 145px; height: 145px; margin: 0 auto; border: 4px solid var(--tile-edge);
    border-radius: 9px;
  }
  .tile-fresh { background: var(--tile-blue); }
  .tile-quality { background: var(--tile-yellow); }
  .tile-local { background: var(--tile-pink); }
  .tile-delivery { background: var(--tile-orange); }
  .tile-weekly { background: var(--tile-green); }
  .feature-label {
    margin-top: 12px; font-family: "Rosarivo", serif; font-size: 18px;
    line-height: 22px; color: var(--label-green);
  }
  .feature-label.rounded { font-family: "Delius", sans-serif; letter-spacing: 1px; }

  .blog-teaser {
    left: 745px; top: 666px; font-family: "Fondamento", cursive; font-size: 12px; line-height: 15px; color: #222;
  }
  .blog-teaser .blog-title { color: var(--blog-teal); }

  .footer-rule { left: 0; top: 933px; width: 1095px; height: 2px; background: #e9e3ee; }
  .site-footer { left: 0; top: 935px; width: 1095px; height: 253px; background: var(--footer-bg); }
  .footer-col {
    position: absolute; top: 56px; font-size: 13.5px; line-height: 18px; color: var(--footer-text);
    letter-spacing: 0.3px;
  }
  .footer-col h3 { font-size: 14px; font-weight: 700; }
  .col-about { left: 146px; width: 210px; }
  .col-contact { left: 437px; }
  .col-news { left: 710px; width: 220px; }
  .socials { position: absolute; left: 145px; top: 156px; display: flex; gap: 9px; }
  .socials span { width: 22px; height: 22px; border-radius: 50%; background: #d7d2db; }
  .newsletter-form { position: absolute; left: 709px; top: 128px; display: flex; align-items: center; }
  .newsletter-input {
    width: 177px; height: 22px; background: #7c6d87; color: #f1ecf4;
    font-size: 13.5px; padding: 1px 6px; letter-spacing: 0.5px;
  }
  .newsletter-btn { margin-left: 10px; color: #bdb3c5; font-size: 13.5px; letter-spacing: 0.5px; }
  .copyright {
    position: absolute; left: 0; width: 1095px; top: 234px; text-align: center;
    font-size: 13.5px; color: #b6a9c0; letter-spacing: 0.5px;
  }
  .bottom-bar { left: 0; top: 1188px; width: 1095px; height: 12px; background: #0c0410; }
</style>
</head>
<body>

  <div class="abs corner-flourish" role="img" aria-label="Golden swirl flourish in the corner"></div>
  <nav class="main-nav">
    <a class="nav-home" href="#">Home</a>
    <a class="nav-shop" href="#">Shop</a>
    <a class="nav-curated" href="#">Curated</a>
    <a class="nav-about" href="#">About Us</a>
  </nav>

  <div class="abs search-box">Search Store
    <svg width="16" height="16" viewBox="0 0 16 16" fill="none" stroke="#fff" stroke-width="1.4"><circle cx="6.5" cy="6.5" r="5"/><line x1="10.2" y1="10.2" x2="15" y2="15"/></svg>
  </div>
  <div class="abs cart-summary"><span>0 items</span><span>$0.0</span></div>
  <div class="abs view-cart">View Cart</div>

  <div class="abs crest-ornament" role="img" aria-label="Golden scroll ornament above the shop name"></div>
  <div class="abs logo-frame">
    <div class="logo-plate">BRISA PETALS</div>
  </div>

  <div class="abs content-frame"><div class="content-panel"></div></div>
  <h1 class="abs page-title">Meet Brisa</h1>
  <p class="abs intro">
    Based in San Diego, Cali - Brisa Petals has fresh and cool in mind.<br>
    Your recipient won't be disappointed. Done are the days of paying for lame bouquets.<br>
    We provide farm fresh flowers delivered same-day for any occasion:
  </p>

  <div class="feature" style="left:187px; top:400px;">
    <div class="tile tile-fresh" role="img" aria-label="Fresh cut flower stem illustration"></div>
    <div class="feature-label">Fresh Cut</div>
  </div>
  <div class="feature" style="left:440px; top:400px;">
    <div class="tile tile-quality" role="img" aria-label="High quality emblem illustration"></div>
    <div class="feature-label">High Quality</div>
  </div>
  <div class="feature" style="left:710px; top:400px;">
    <div class="tile tile-local" role="img" aria-label="Heart illustration marked San Diego"></div>
    <div class="feature-label">San Diego Based</div>
  </div>
  <div class="feature" style="left:187px; top:629px;">
    <div class="tile tile-delivery" role="img" aria-label="Delivery truck illustration"></div>
    <div class="feature-label">Same Day Delivery<br>If Ordered By 2 pm</div>
  </div>
  <div class="feature" style="left:420px; top:629px; width:240px;">
    <div class="tile tile-weekly" role="img" aria-label="Weekly and corporate delivery emblem illustration"></div>
    <div class="feature-label rounded">Weekly And Corpoate<br>Delivery Availble</div>
  </div>

  <div class="abs blog-teaser">
    <div class="blog-title">Our blog</div>
    <div>First Post</div>
    <div>May 26, 2014</div>
  </div>

  <div class="abs footer-rule"></div>
  <footer class="abs site-footer">
    <div class="footer-col col-about">
      <h3>Meet Brisa</h3>
      <p>Based in Hillcrest, San Diego We offer farm fresh, curated, cool, and same day delivery flower bouquets.</p>
    </div>
    <div class="socials"><span></span><span></span><span></span></div>
    <div class="footer-col col-contact">
      <h3>Reach Brisa</h3>
      <p>2215 Juniper Lane<br>San Diego, CA 92104<br>Email: hello@brisapetals.example<br>Phone: 619-555-0142</p>
    </div>
    <div class="footer-col col-news">
      <h3>Newsletter</h3>
      <p>We promise to only send you good things like discounts!</p>
    </div>
    <div class="newsletter-form">
      <div class="newsletter-input">your@email.com</div>
      <div class="newsletter-btn">Sign up</div>
    </div>
    <div class="copyright">Copyright © 2014 brisapetals of San Diego.</div>
  </footer>
  <div class="abs bottom-bar"></div>

</body>
</html>
```